SkyvornQ Business Cards and Stationary Design

Need a design for our business cards and stationary. I want to carry on the theme of the logo. I want the business cards to have a design on the back. I would like the business cards and the stationary to carry the same theme, design scheme, and branding

Target Market(s)

Airlines and Maintenance Facilities

Industry/Entity Type

Aviation

Contact Information for Business Card

Name
Position Title
Address: 4827 Trellis Hollow Road, Fort Pierce, Florida, 34951
Office Number
Mobile Number
Email
Website

Font styles to use
Serif
Sans Serif

Colors

Designer to choose colors to be used in the design.

```html
<!DOCTYPE html>
<html lang="en">
<head>
<meta charset="utf-8">
<title>SkyvornQ Business Card</title>
<link rel="stylesheet" href="https://fonts.googleapis.com/css2?family=Open+Sans:wght@400;700&display=swap">
<style>
  :root {
    --navy: #0b2a5b;
    --blue: #1673c4;
    --sky: #2ba3e0;
    --ink: #3a3f47;
    --paper: #ffffff;
    --backdrop: #e9e6e3;
  }
  * { box-sizing: border-box; margin: 0; padding: 0; }
  html, body {
    width: 1200px; height: 997px; overflow: hidden;
    background: var(--backdrop);
    font-family: "Open Sans", Arial, sans-serif;
  }
  .sheet { position: relative; width: 1200px; height: 997px; }
  .card {
    position: absolute; width: 600px; height: 343px;
    background: var(--paper);
    box-shadow: 0 6px 18px rgba(0,0,0,0.12);
    overflow: hidden;
  }
  .card--front { left: 300px; top: 110px; }
  .card--back { left: 300px; top: 544px; }

  .card__wave { position: absolute; inset: 0; width: 100%; height: 100%; }

  .brand { position: absolute; display: flex; align-items: center; gap: 12px; }
  .brand__dot { width: 38px; height: 38px; border-radius: 50%; background: var(--blue); }
  .brand__name { font-weight: 700; color: var(--navy); letter-spacing: 4px; font-size: 30px; }
  .card--front .brand { left: 58px; top: 104px; }

  .person { position: absolute; right: 34px; top: 28px; text-align: right; }
  .person__name { font-weight: 700; color: var(--navy); font-size: 16px; }
  .person__role { color: var(--sky); font-size: 12px; }

  .contact {
    position: absolute; right: 34px; top: 84px; text-align: right;
    font-size: 11px; line-height: 15px; color: var(--ink);
  }
  .contact__address { margin-bottom: 8px; }
  .contact__row { display: flex; justify-content: flex-end; align-items: center; gap: 6px; }
  .contact__icon { width: 10px; height: 10px; }

  .card__web {
    position: absolute; left: 40px; bottom: 22px;
    color: var(--paper); font-size: 13px; letter-spacing: 2.5px;
  }

  .card--back .brand { left: 0; right: 0; top: 118px; justify-content: center; }
  .card--back .brand__name { font-size: 36px; letter-spacing: 5px; }
  .card--back .brand__dot { width: 46px; height: 46px; }
  .card--back .card__web {
    left: 0; right: 0; bottom: auto; top: 196px; text-align: center;
    color: var(--ink); font-size: 14px; letter-spacing: 3px;
  }
</style>
</head>
<body>
<main class="sheet">
  <section class="card card--front">
    <svg class="card__wave" viewBox="0 0 600 343" preserveAspectRatio="none" aria-hidden="true">
      <path d="M0 282 C140 268 250 260 350 236 C440 214 520 206 600 204 L600 343 L0 343 Z" fill="var(--navy)"/>
      <path d="M110 275 C230 256 320 230 410 210 C490 194 550 191 600 191 L600 204 C520 206 440 214 350 236 C260 258 190 268 110 275 Z" fill="var(--blue)"/>
      <path d="M250 262 C350 240 450 212 600 198" stroke="var(--paper)" stroke-width="1.5" fill="none"/>
      <path d="M300 244 C400 216 480 196 600 186" stroke="var(--sky)" stroke-width="2" fill="none"/>
    </svg>

    <div class="brand">
      <span class="brand__dot"></span>
      <span class="brand__name">SKYVORNQ</span>
    </div>

    <div class="person">
      <p class="person__name">MARCUS DELVEY</p>
      <p class="person__role">President</p>
    </div>

    <div class="contact">
      <p class="contact__address">4827 Trellis Hollow Road,<br>Fort Pierce, Florida, 34951</p>
      <p class="contact__row">+971 4 528 3094
        <svg class="contact__icon" viewBox="0 0 10 10"><path d="M2 1 L4 3 L3 4 C4 6 5 7 6 7 L7 6 L9 8 L8 9 C4 9 1 6 1 2 Z" fill="var(--blue)"/></svg>
      </p>
      <p class="contact__row">+971 50 714 2859
        <svg class="contact__icon" viewBox="0 0 10 10"><rect x="2.5" y="0.5" width="5" height="9" rx="1" fill="none" stroke="var(--blue)"/></svg>
      </p>
      <p class="contact__row">info@skyvornq.com
        <svg class="contact__icon" viewBox="0 0 10 10"><rect x="0.5" y="2" width="9" height="6" fill="var(--blue)"/><path d="M0.5 2 L5 5.5 L9.5 2" stroke="var(--paper)" fill="none"/></svg>
      </p>
    </div>

    <p class="card__web">www.skyvornq.com</p>
  </section>

  <section class="card card--back">
    <div class="brand">
      <span class="brand__dot"></span>
      <span class="brand__name">SKYVORNQ</span>
    </div>
    <p class="card__web">www.skyvornq.com</p>
  </section>
</main>
</body>
</html>
```